We are building a website where users come to see what skills they will need for their career. The content of the page is data-driven, so the site should have the feel of a set of data dashboards. The data is collected and processed using machine learning. The main idea is for the user to come in and spend some minutes exploring, scrolling and clicking around.
The task is to design a website with four pages:
Front page
Early career page
Skill trends page
Skills Page
Each of these is described in attached files, along with example data
We need the resulting files to be exported also to uncompressed PNG, and in the case of vector graphics, to SVG.
Target Market(s)
People Looking to start a Career and Policy makers.
Industry/Entity Type
Human Resource
Number of Pages Required
4 page
Look and feel

```html
<!DOCTYPE html>
<html lang="en">
<head>
<meta charset="utf-8">
<title>SkillScope – Your personal guide to the skill trends</title>
<link href="https://fonts.googleapis.com/css2?family=Montserrat:wght@600;700;800&family=Open+Sans:wght@400;600;700&display=swap" rel="stylesheet">
<style>
:root{
  --navy:#0b1633;
  --royal:#1f3a9b;
  --green:#76c043;
  --ink:#1b1e2b;
  --body:#3a3f4e;
  --muted:#8a90a0;
  --line:#e3e6ee;
  --paper:#ffffff;
  --mist:#f1f3f7;
}
*{box-sizing:border-box;margin:0;padding:0}
html,body{width:1200px;height:4832px;overflow:hidden}
body{font-family:"Open Sans",Arial,sans-serif;color:var(--body);background:var(--paper);position:relative}
h1,h2,h3,.brand,.btn{font-family:"Montserrat",Arial,sans-serif}
section,header,footer{position:absolute;left:0;width:1200px}
.btn{display:inline-block;border-radius:40px;font-weight:700;font-size:15px;letter-spacing:.5px;text-transform:uppercase;text-align:center;white-space:nowrap}
.btn-green{background:var(--green);color:#fff;padding:16px 40px}

/* hero */
.hero{top:0;height:800px;background:linear-gradient(100deg,#070f24 0%,#0f1f45 55%,#1a3567 100%);overflow:hidden}
.hero-visual{position:absolute;right:0;top:0;width:680px;height:800px;background:radial-gradient(circle at 55% 45%,#3f6fa8 0%,#1d3a6a 40%,rgba(15,31,69,0) 75%)}
.nav{position:absolute;top:40px;left:40px;right:100px;height:60px;display:flex;align-items:center}
.brand{color:#fff;font-weight:800;font-size:40px;white-space:nowrap}
.nav-links{display:flex;gap:30px;margin-left:110px;list-style:none}
.nav-links li{color:#fff;font-size:19px;font-weight:600;white-space:nowrap}
.nav-cta{margin-left:auto;border:2px solid #fff;color:#fff;padding:12px 22px;font-size:14px}
.hero-title{position:absolute;left:40px;top:330px;color:#fff;font-size:80px;font-weight:800}
.hero-sub{position:absolute;left:40px;top:440px;width:560px;color:#dfe8ff;font-size:42px;font-weight:700;line-height:1.22;font-family:"Montserrat",Arial,sans-serif}
.hero .btn-green{position:absolute;left:40px;top:668px}
.dots{position:absolute;left:40px;top:750px;display:flex;gap:12px}
.dots span{width:14px;height:14px;border-radius:50%;background:#6f7d9c}
.dots span:first-child{background:var(--green)}

/* motivation */
.motivation{top:800px;height:800px}
.section-title{text-align:center;color:var(--ink);font-weight:800}
.motivation h2{margin-top:60px;font-size:58px}
.motivation p{width:900px;margin:30px auto 0;text-align:center;font-size:20px;line-height:1.55;color:var(--ink)}
.dash{position:absolute;background:#fff;border-radius:14px;box-shadow:0 8px 30px rgba(20,30,60,.18);overflow:hidden}
.dash-main{left:130px;top:430px;width:630px;height:290px}
.dash-side{left:780px;top:330px;width:360px;height:390px}
.dash-search{position:absolute;left:22px;top:22px;width:470px;height:46px;border:1px solid var(--line);border-radius:8px;font-size:14px;padding:13px 16px;color:var(--muted)}
.dash-go{position:absolute;left:506px;top:22px;width:46px;height:46px;border-radius:8px;background:var(--mist)}
.year-badge{position:absolute;width:60px;height:60px;border-radius:50%;background:var(--royal);color:#fff;font-size:13px;font-weight:700;display:flex;align-items:center;justify-content:center;font-family:"Montserrat",Arial,sans-serif}
.legend{position:absolute;left:22px;top:90px;width:590px;display:flex;gap:14px;font-size:10px;font-weight:600;color:var(--ink);white-space:nowrap}
.legend span{display:flex;align-items:center;gap:5px}
.legend i{width:12px;height:3px;display:inline-block}
.chart{position:absolute;left:22px;top:112px}
.side-lines{position:absolute;left:22px;top:30px;width:310px}
.side-lines div{height:8px;background:var(--line);border-radius:4px;margin-bottom:10px}
.side-row{position:absolute;left:22px;width:316px;font-size:12px;color:var(--body);display:flex;gap:8px;flex-wrap:wrap}
.tag{border:1px solid #c5cdf0;border-radius:4px;padding:3px 8px;color:var(--royal)}
.side-box{position:absolute;left:22px;top:260px;width:316px;height:90px;border:1px solid var(--line);border-radius:8px}

/* intro */
.intro{top:1600px;height:620px;background:var(--royal)}
.intro h2{margin-top:64px;font-size:50px;color:#fff;text-align:center}
.intro h3{margin-top:34px;font-size:40px;color:#fff;text-align:center;font-weight:700}
.challenge{position:absolute;top:240px;width:510px;height:340px;background:#fff;display:flex;padding:30px 28px;gap:24px}
.challenge-1{left:70px}.challenge-2{left:620px}
.challenge-icon{flex:0 0 150px;height:150px;border-radius:50%;background:radial-gradient(circle,#dfe6fb 0%,#eef1fb 70%)}
.challenge p{font-size:15px;line-height:1.55;color:var(--ink)}

/* method */
.method{top:2220px;height:580px;background:#fff}
.method-visual{position:absolute;left:0;top:0;width:560px;height:580px;background:linear-gradient(135deg,#1d8fe0 0%,#38b3f0 55%,#7fd0f7 100%)}
.method h2{position:absolute;left:660px;top:70px;font-size:56px;color:var(--ink);font-weight:800}
.method p{position:absolute;left:660px;top:160px;width:500px;font-size:14.5px;line-height:1.6;color:var(--body)}
.method .btn-green{position:absolute;left:660px;top:490px;padding:14px 34px}

/* about */
.about{top:2800px;height:1120px}
.about h2{margin-top:50px;font-size:62px}
.about p{width:940px;margin:26px auto 0;text-align:center;font-size:19px;line-height:1.55;color:var(--ink)}
.about p a{color:var(--ink);font-weight:700;text-decoration:none}
.team-band{position:absolute;left:0;top:700px;width:1200px;height:300px;background:var(--mist)}
.member{position:absolute;top:600px;width:260px;height:430px;background:#fff;border-radius:130px 130px 130px 130px;box-shadow:0 12px 30px rgba(20,30,60,.16);text-align:center;overflow:hidden}
.member-1{left:180px}.member-2{left:470px}.member-3{left:760px}
.member-photo{width:200px;height:200px;margin:18px auto 0;border-radius:50%;background:linear-gradient(160deg,#c9ccd3 0%,#8e96a6 100%)}
.member h3{margin-top:14px;font-size:24px;color:var(--ink);font-weight:700}
.member .role{font-size:14px;color:var(--body);margin-top:2px}
.member .bio{width:190px;margin:10px auto 0;font-size:13px;line-height:1.45;color:var(--body)}
.about .btn-green{position:absolute;left:520px;top:1058px;width:160px;padding:16px 0}

/* partners */
.partners{top:3920px;height:400px}
.partners h2{margin-top:24px;font-size:58px}
.partner-row{position:absolute;top:150px;left:0;width:1200px;display:flex;justify-content:center;gap:140px}
.partner{display:flex;align-items:center;gap:18px;font-family:"Open Sans",Arial,sans-serif;font-weight:700;font-size:24px;color:var(--ink);white-space:nowrap}
.partner .mark{flex:0 0 120px;width:120px;height:120px;background:#1f3b8f}
.partner-2 .mark{border-radius:50%;background:#b5343a}

/* contact */
.contact{top:4320px;height:512px;background:var(--royal)}
.contact h2{margin-top:86px;font-size:56px;color:#fff;text-align:center}
.contact-list{position:absolute;top:220px;left:160px;right:120px;display:flex;justify-content:space-between;list-style:none}
.contact-list li{display:flex;gap:16px;align-items:flex-start;color:#fff;font-size:17px;line-height:1.45;width:270px}
.contact-list b{display:block;font-weight:700}
.contact-icon{flex:0 0 44px;height:44px}
.contact hr{position:absolute;top:345px;left:0;width:1200px;border:0;border-top:1px solid rgba(255,255,255,.3)}
.legal{position:absolute;top:378px;width:1200px;text-align:center;color:#fff;font-size:15px}
.legal u{text-decoration:underline}
.social{position:absolute;top:430px;left:540px;display:flex;gap:16px}
.social span{width:40px;height:40px;border-radius:50%;border:2px solid #fff}
</style>
</head>
<body>

<header class="hero">
  <div class="hero-visual" role="img" aria-label="Humanoid robot touching a glowing data interface"></div>
  <nav class="nav">
    <div class="brand">SkillScope</div>
    <ul class="nav-links">
      <li>Home</li><li>Early career</li><li>Skill trends</li><li>Skills</li><li>Contact</li>
    </ul>
    <span class="btn nav-cta">Get started</span>
  </nav>
  <h1 class="hero-title">SkillScope</h1>
  <p class="hero-sub">Your personal guide to the skill trends on the job market</p>
  <span class="btn btn-green">Learn more</span>
  <div class="dots"><span></span><span></span><span></span><span></span></div>
</header>

<section class="motivation">
  <h2 class="section-title">MOTIVATION</h2>
  <p>We enable deep and unbiased analysis of the skill demands in the job market. Using deep learning techniques, we achieve understanding of job advertisements to extract the most relevant information for you. We combine these analysis with the most complete structural knowledge repositories to deliver analytics, discover trends and provide recommendations for personal professional development, as well as insightful job market overviews!</p>

  <div class="dash dash-side">
    <div class="side-lines"><div style="width:40%"></div><div></div><div style="width:85%"></div><div style="width:70%"></div></div>
    <div class="side-row" style="top:120px"><span class="tag">Data analysis</span><span class="tag">Teamwork</span><span class="tag">Python</span></div>
    <div class="side-row" style="top:160px"><span class="tag">Project planning</span><span class="tag">Statistics</span></div>
    <div class="side-row" style="top:210px">Related occupations and trending skills</div>
    <div class="side-box"></div>
  </div>
  <div class="year-badge" style="left:1110px;top:300px">2021</div>

  <div class="dash dash-main">
    <div class="dash-search">Enter a skill or a job title</div>
    <div class="dash-go"></div>
    <div class="legend">
      <span><i style="background:#e0523f"></i>Project management</span>
      <span><i style="background:#2a7be0"></i>Pedagogy</span>
      <span><i style="background:#f2a33a"></i>Office software</span>
      <span><i style="background:#3bb273"></i>Marketing techniques</span>
      <span><i style="background:#8a55c9"></i>Human resources</span>
    </div>
    <svg class="chart" width="586" height="166" viewBox="0 0 730 170" preserveAspectRatio="none">
      <g stroke="#e3e6ee" stroke-width="1">
        <line x1="0" y1="20" x2="730" y2="20"/><line x1="0" y1="60" x2="730" y2="60"/><line x1="0" y1="100" x2="730" y2="100"/><line x1="0" y1="140" x2="730" y2="140"/>
      </g>
      <g fill="none" stroke-width="2.5">
        <polyline stroke="#e0523f" points="0,40 90,50 180,35 270,55 360,45 450,70 540,60 630,80 720,70"/>
        <polyline stroke="#2a7be0" points="0,70 90,65 180,80 270,72 360,90 450,85 540,100 630,95 720,110"/>
        <polyline stroke="#f2a33a" points="0,95 90,100 180,90 270,105 360,98 450,110 540,104 630,118 720,112"/>
        <polyline stroke="#3bb273" points="0,115 90,110 180,118 270,108 360,120 450,115 540,125 630,120 720,128"/>
        <polyline stroke="#8a55c9" points="0,128 90,132 180,125 270,134 360,130 450,138 540,133 630,140 720,136"/>
      </g>
      <g font-size="13" fill="#1b1e2b" font-family="Open Sans, Arial, sans-serif" font-weight="600">
        <text x="0" y="164">2013</text><text x="175" y="164">2015</text><text x="355" y="164">2017</text><text x="535" y="164">2019</text><text x="690" y="164">2021</text>
      </g>
    </svg>
  </div>
  <div class="year-badge" style="left:735px;top:405px">2021</div>
</section>

<section class="intro">
  <h2>We Introduce Our Application</h2>
  <h3>Challenges</h3>
  <div class="challenge challenge-1">
    <div class="challenge-icon" role="img" aria-label="Line illustration of a person surrounded by gears"></div>
    <p>Choosing the correct occupation plays an increasingly important role in our lives. Nowadays we consider an occupation as one of our fundamental rights. Yet, with the complexity of the modern technologies and job markets it is challenging to guarantee equal access to the market for everyone.</p>
  </div>
  <div class="challenge challenge-2">
    <div class="challenge-icon" role="img" aria-label="Line illustration of a profile document under a magnifier"></div>
    <p>The challenges include the knowledge of languages, personal traits, different understanding of requirements and different assessments of personal strengths. On the other end, business owners and recruitment professionals invest lots of effort to find suitable candidates for their job openings. How do we improve the situation, overcome the challenges and enable efficient, unbiased analysis of job market?</p>
  </div>
</section>

<section class="method">
  <div class="method-visual" role="img" aria-label="Illustration of a robot working at a laptop in front of code lines"></div>
  <h2>How we do this</h2>
  <p>We employ machine learning. Machines do not have personal preferences or biases. The impressive progress of natural language processing and deep neural networks power our algorithms to precisely recognize and extract the most important pieces of information. We use manually designed ontologies that set the frames of the analysis and guide the machine in this process. However, machines (and also we ourselves) still miss a lot of background information about our complex professional world — no one is perfect (yet). To fill in this gap we use the most complete structural knowledge sources to serve as background knowledge and provide additional information about the subject area. The combination of these two methodologies yields the best results.</p>
  <span class="btn btn-green">Learn more</span>
</section>

<section class="about">
  <h2 class="section-title">About us</h2>
  <p>This application is a free social project powered by 3 enthusiast. We are experts in Natural Language Processing and Semantic Web with a record of 50+ scientific publications at top conferences and journals <a>(https://papers.example.org/team/k0jr9w)</a> <a>(https://papers.example.org/team/ho0pta)</a>. We also have training and work experience in HR, and, most importantly passion for the job market. We all have migrant background and we know how difficult and important it might be to find your place in any new professional environment. Therefore, we strive to provide better professional opportunities, equal access and fair treatment for everyone.</p>
  <p>At the moment the project is completely funded by us. This not only includes the maintenance and further development, but also the costs of the infrastructure. If you like it and want us to continue, please, support us. Your every donation counts.</p>
  <div class="team-band"></div>
  <div class="member member-1">
    <div class="member-photo" role="img" aria-label="Portrait photo of team member"></div>
    <h3>John Doe</h3><div class="role">Nemo enim ipsam</div>
    <div class="bio">Nemo enim ipsam voluptatem quia voluptas sit aspernatur aut odit aut fugit, sed quia consequuntur magni dolores eos qui</div>
  </div>
  <div class="member member-2">
    <div class="member-photo" role="img" aria-label="Portrait photo of team member"></div>
    <h3>John Doe</h3><div class="role">Nemo enim ipsam</div>
    <div class="bio">Nemo enim ipsam voluptatem quia voluptas sit aspernatur aut odit aut fugit, sed quia consequuntur magni dolores eos qui</div>
  </div>
  <div class="member member-3">
    <div class="member-photo" role="img" aria-label="Portrait photo of team member"></div>
    <h3>John Doe</h3><div class="role">Nemo enim ipsam</div>
    <div class="bio">Nemo enim ipsam voluptatem quia voluptas sit aspernatur aut odit aut fugit, sed quia consequuntur magni dolores eos qui</div>
  </div>
  <span class="btn btn-green">Donate</span>
</section>

<section class="partners">
  <h2 class="section-title">Powered by</h2>
  <div class="partner-row">
    <div class="partner partner-1"><span class="mark"></span>Union Research Fund</div>
    <div class="partner partner-2"><span class="mark"></span>OpenFacts</div>
  </div>
</section>

<footer class="contact">
  <h2>CONTACT US</h2>
  <ul class="contact-list">
    <li>
      <svg class="contact-icon" viewBox="0 0 44 44"><circle cx="22" cy="22" r="21" fill="#fff"/><path d="M22 11a7 7 0 0 0-7 7c0 5 7 14 7 14s7-9 7-14a7 7 0 0 0-7-7z" fill="#1f3a9b"/><circle cx="22" cy="18" r="2.6" fill="#fff"/></svg>
      <span>576 enim ipsam voluptatem quia volup</span>
    </li>
    <li>
      <svg class="contact-icon" viewBox="0 0 44 44"><circle cx="22" cy="22" r="21" fill="#fff"/><path d="M15 13l5 0 2 6-3 2a12 12 0 0 0 5 5l2-3 6 2 0 5c0 1-1 2-2 2A18 18 0 0 1 13 15c0-1 1-2 2-2z" fill="#1f3a9b"/></svg>
      <span><b>Phone:</b>800 555 0142</span>
    </li>
    <li>
      <svg class="contact-icon" viewBox="0 0 44 44"><circle cx="22" cy="22" r="21" fill="#fff"/><rect x="12" y="15" width="20" height="14" rx="2" fill="#1f3a9b"/><path d="M12 16l10 7 10-7" fill="none" stroke="#fff" stroke-width="1.6"/></svg>
      <span><b>Email:</b>info@skillscope.example</span>
    </li>
  </ul>
  <hr>
  <div class="legal">SkillScope © 2021 All Rights Reserved | <u>Privacy Policy</u> | <u>Terms</u></div>
  <div class="social"><span></span><span></span><span></span></div>
</footer>

</body>
</html>
```